Business Card Design for Varomir Facility Services

We are looking for a Business Card Design for the Company "Varomir Facility Services."
Front side:
- Company Logo (small)
- Company Name, address, pohone, website and personal data.
- white background, for text e.g. company colors (blue or green like in the logo)
Please use following data:
Company data:
Varomir Facility Services Kostelac
Birkenhaldweg 14
6330 Cham
www.varomir-fs.ch
Person data:
Tarik Kostelac
Geschäftsführer
+41 76 519 47 83
info@varomir-fs.ch
Back side:
could be colored in blue or green
please use a big logo sing and some smaller icons to say what is all beeing offered in facility services, like cleaning, maintenance cleaning
industrial cleaning, caretaking, gardening, disposal. There is no need for everyone of the icons if there are similar or an icon is standing for more of them.
colors to use:
blue: HEX 246BB0
green: HEX 52B33E

```html
<!DOCTYPE html>
<html lang="de">
<head>
<meta charset="utf-8">
<title>Varomir Facility Services – Business Card</title>
<link href="https://fonts.googleapis.com/css2?family=Lato:wght@400;700&display=swap" rel="stylesheet">
<style>
  :root {
    --brand-blue: #246BB0;
    --brand-green: #52B33E;
    --card-light: #e4e5e7;
    --ink: #1f1f1f;
    --white: #ffffff;
    --rule-light: rgba(255,255,255,0.55);
    --rule-dark: #b9bbbe;
    --backdrop: #ecebe8;
  }
  * { margin: 0; padding: 0; box-sizing: border-box; }
  html, body {
    width: 1200px; height: 900px; overflow: hidden;
    background: var(--backdrop);
    font-family: "Lato", Arial, sans-serif;
  }
  .canvas { position: relative; width: 1200px; height: 900px; }
  .card { position: absolute; width: 556px; height: 343px; }
  .card--contact { left: 330px; top: 90px; background: var(--brand-blue); color: var(--white); }
  .card--services { left: 330px; top: 469px; background: var(--card-light); color: var(--ink); }

  .centered { position: absolute; left: 0; width: 100%; text-align: center; white-space: nowrap; }
  .person-name { top: 70px; font-size: 20px; font-weight: 700; letter-spacing: 0.5px; }
  .person-role { top: 92px; font-size: 15px; }
  .contact-icons { position: absolute; left: 188px; top: 122px; width: 180px; height: 24px; }
  .contact-line { font-size: 15.5px; }
  .contact-phone { top: 152px; }
  .contact-mail { top: 172px; }
  .contact-web { top: 192px; }
  .rule-light { position: absolute; left: 182px; top: 222px; width: 190px; height: 1px; background: var(--rule-light); }
  .company-name { top: 231px; font-size: 16px; }
  .company-address { top: 251px; font-size: 15.5px; }

  .wordmark { position: absolute; left: 0; top: 128px; width: 100%; display: flex; justify-content: center; align-items: center; gap: 12px; }
  .wordmark-dot { width: 26px; height: 26px; border-radius: 50%; background: var(--brand-green); }
  .wordmark-name { font-size: 30px; font-weight: 700; color: var(--brand-blue); letter-spacing: 1px; }
  .service-divider { position: absolute; left: 56px; top: 235px; width: 446px; height: 34px; }
  .service-list { font-size: 14.5px; letter-spacing: 0.2px; }
  .service-list--first { top: 274px; }
  .service-list--second { top: 292px; }
</style>
</head>
<body>
<main class="canvas">
  <section class="card card--contact">
    <div class="centered person-name">TARIK KOSTELAC</div>
    <div class="centered person-role">Geschäftsführer</div>
    <svg class="contact-icons" viewBox="0 0 180 24" aria-hidden="true">
      <line x1="0" y1="12" x2="50" y2="12" stroke="rgba(255,255,255,0.55)" stroke-width="1"/>
      <line x1="128" y1="12" x2="178" y2="12" stroke="rgba(255,255,255,0.55)" stroke-width="1"/>
      <circle cx="63" cy="12" r="11" fill="#fff"/>
      <path d="M57 9 q6 -5 12 0 l-2 2 h-8 z M58 12 h10 v5 h-10 z" fill="#246BB0"/>
      <circle cx="89" cy="12" r="11" fill="#fff"/>
      <rect x="82" y="7" width="14" height="10" rx="1" fill="#246BB0"/>
      <path d="M82 7 l7 6 l7 -6" fill="none" stroke="#fff" stroke-width="1.2"/>
      <circle cx="115" cy="12" r="11" fill="#fff"/>
      <circle cx="115" cy="12" r="6.5" fill="none" stroke="#246BB0" stroke-width="1.6"/>
      <path d="M108.5 12 h13 M115 5.5 q-4 6.5 0 13 M115 5.5 q4 6.5 0 13" fill="none" stroke="#246BB0" stroke-width="1.2"/>
    </svg>
    <div class="centered contact-line contact-phone">+41 76 519 47 83</div>
    <div class="centered contact-line contact-mail">info@varomir-fs.ch</div>
    <div class="centered contact-line contact-web">www.varomir-fs.ch</div>
    <div class="rule-light"></div>
    <div class="centered company-name">Varomir Facility Services Kostelac</div>
    <div class="centered company-address">Birkenhaldweg 14, 6330 Cham</div>
  </section>

  <section class="card card--services">
    <div class="wordmark">
      <span class="wordmark-dot"></span>
      <span class="wordmark-name">Varomir Facility Services</span>
    </div>
    <svg class="service-divider" viewBox="0 0 446 34" aria-hidden="true">
      <line x1="0" y1="17" x2="192" y2="17" stroke="#b9bbbe" stroke-width="1"/>
      <line x1="256" y1="17" x2="446" y2="17" stroke="#b9bbbe" stroke-width="1"/>
      <circle cx="224" cy="17" r="16" fill="#246BB0"/>
      <line x1="233" y1="6" x2="224" y2="16" stroke="#fff" stroke-width="2" stroke-linecap="round"/>
      <path d="M222 14 l5 5 l-7 9 l-7 -3 z" fill="#fff"/>
      <path d="M216 22 l6 3 M219 19 l5 3" stroke="#246BB0" stroke-width="1"/>
    </svg>
    <div class="centered service-list service-list--first">CLEANING &nbsp;|&nbsp; MAINTENANCE CLEANING &nbsp;|&nbsp; INDUSTRIAL CLEANING</div>
    <div class="centered service-list service-list--second">CARETAKING &nbsp;|&nbsp; GARDENING &nbsp;|&nbsp; DISPOSAL</div>
  </section>
</main>
</body>
</html>
```